Business Card Design - Amberfield Court

We are looking at a new design for our business cards that has a modern and professional look. We run a residential aged care facility focussing on the care of residents. The cards will be used for potential clients, consultants and business opportunities in this sector. Blue and white is our main colours and would to see these colours incorporated in the design.
Industry/Entity Type
Business
Contact Information for Business Card
Amberfield Court, Darren Walsh, dwalsh@amberfieldcourt.com.au, Finance Manager, 0472 639 208, BCom, 37 Marrabel Crescent, Brindle Vale, Qld 4093.
Look and feel
Each slider illustrates characteristics of the customer's brand and the style your logo design should communicate.

```html
<!DOCTYPE html>
<html lang="en">
<head>
<meta charset="utf-8">
<title>Amberfield Court – Business Card</title>
<link rel="stylesheet" href="https://fonts.googleapis.com/css2?family=Oswald:wght@400;600&family=Open+Sans:wght@400;600&display=swap">
<style>
  :root {
    --backdrop: #ece9e5;
    --card-white: #fbfbfb;
    --brand-blue: #4b7e9b;
    --ink-blue: #3d5f73;
    --text-blue: #6a93ab;
    --band-taupe: #b8ada5;
    --band-text: #ffffff;
    --icon-taupe: #a79a90;
    --mark-white: #ffffff;
  }
  * { box-sizing: border-box; margin: 0; padding: 0; }
  html, body {
    width: 1200px; height: 1023px; overflow: hidden;
    background: var(--backdrop);
  }
  .canvas { position: relative; width: 1200px; height: 1023px; }

  .card {
    position: absolute; width: 600px; height: 343px;
    border-radius: 4px; overflow: hidden;
    box-shadow: 0 6px 18px rgba(0,0,0,0.18);
  }
  .card--front { left: 70px; top: 130px; background: var(--card-white); }
  .card--back { left: 530px; top: 550px; background: var(--brand-blue); }

  /* brand lockup */
  .brand-mark { position: absolute; border-radius: 50%; }
  .card--front .brand-mark { left: 50px; top: 44px; width: 112px; height: 112px; background: var(--brand-blue); }
  .card--back .brand-mark { left: 440px; top: 84px; width: 120px; height: 120px; background: var(--mark-white); }

  .brand-name {
    position: absolute;
    font-family: "Oswald", sans-serif; font-weight: 400;
    font-size: 34px; letter-spacing: 3px; text-transform: uppercase;
    line-height: 1;
  }
  .card--front .brand-name { left: 184px; top: 116px; color: var(--ink-blue); }
  .card--back .brand-name { left: 60px; top: 146px; color: var(--mark-white); }

  .tagline-band {
    position: absolute; height: 30px; background: var(--band-taupe);
    display: flex; align-items: center;
    font-family: "Open Sans", sans-serif; font-size: 17px;
    color: var(--band-text); letter-spacing: 0.3px;
  }
  .card--front .tagline-band { left: 0; right: 0; top: 164px; padding-left: 184px; }
  .card--back .tagline-band { left: 40px; width: 370px; top: 194px; padding-left: 20px; }

  /* person */
  .person { position: absolute; right: 30px; top: 28px; }
  .person__name {
    font-family: "Oswald", sans-serif; font-weight: 600;
    font-size: 22px; letter-spacing: 1px; text-transform: uppercase;
    color: var(--ink-blue);
  }
  .person__role {
    font-family: "Open Sans", sans-serif; font-size: 14px;
    color: var(--text-blue);
  }

  /* contact */
  .contact-list {
    position: absolute; left: 184px; top: 214px; list-style: none;
    font-family: "Open Sans", sans-serif; font-size: 14px;
    color: var(--text-blue); line-height: 1.9;
  }
  .contact-list li { display: flex; align-items: center; gap: 10px; }
  .contact-icon { width: 13px; height: 13px; fill: var(--icon-taupe); color: var(--icon-taupe); flex: none; }
</style>
</head>
<body>
<main class="canvas">

  <section class="card card--front" aria-label="Business card front">
    <span class="brand-mark"></span>
    <div class="brand-name">Amberfield Court</div>
    <div class="tagline-band">Comfort, Respect, Belonging</div>

    <div class="person">
      <div class="person__name">Darren Walsh</div>
      <div class="person__role">Finance Manager</div>
    </div>

    <ul class="contact-list">
      <li>
        <svg class="contact-icon" viewBox="0 0 16 16" aria-hidden="true"><path d="M8 1 1 7h2v8h4v-5h2v5h4V7h2z"/></svg>
        BCom, 37 Marrabel Crescent, Brindle Vale, Qld 4093
      </li>
      <li>
        <svg class="contact-icon" viewBox="0 0 16 16" aria-hidden="true"><path d="M1 3h14v10H1z M1 3l7 6 7-6" fill="none" stroke="currentColor" stroke-width="1.6"/></svg>
        dwalsh@amberfieldcourt.com.au
      </li>
      <li>
        <svg class="contact-icon" viewBox="0 0 16 16" aria-hidden="true"><path d="M4 1l2.5 3.5-1.5 1.5a9 9 0 0 0 5 5l1.5-1.5L15 12l-2 3C7 15 1 9 1 3z"/></svg>
        0472 639 208
      </li>
    </ul>
  </section>

  <section class="card card--back" aria-label="Business card back">
    <span class="brand-mark"></span>
    <div class="brand-name">Amberfield Court</div>
    <div class="tagline-band">Comfort, Respect, Belonging</div>
  </section>

</main>
</body>
</html>
```